Accountability Project Graphics

I want to create 10 social media graphics (new Instagram size 4:5 (1080 x 1350 pixels) focusing on our Quilvo Accountability App, using any of the 3 pictures attached. Use the attached pics only, NO RANDOM STOCK PHOTOGRAPHY. For the color scheme, use the landing page colors/fonts (attached).
You can add any of the 3 photos attached but I mainly need BOLD text that includes these headlines and sub-headlines on them.
Please NOTE for all the headlines below, also add this sub-headline on each graphic:
Stay Consistent with RT in Your Pocket!
Here are the headlines:
• Stop Starting Over Every Monday
• You don't need more willpower. You need more support
• Built for women who are tired of doing this alone
• When Motivation Fades, RT Checks In
• The Support System You've Been Missing
• Support When Motivation Disappears
• What if RT Checked in Every Day?
• The Missing Piece Isn't Another Diet
• Eat the food you love. Stay accountable every day.
• One Bad Meal Doesn't Mean You Failed
women over 40 trying to lose weight

```html
<!DOCTYPE html>
<html lang="en">
<head>
<meta charset="UTF-8">
<title>Quilvo Accountability App – Social Graphics</title>
<link rel="stylesheet" href="https://fonts.googleapis.com/css2?family=Montserrat:wght@700;800;900&family=Playfair+Display:ital,wght@0,700;0,900;1,700;1,900&family=Poppins:ital,wght@0,600;0,700;1,600;1,700&display=swap">
<style>
:root{
  --sheet:#5a5a5a;
  --plum:#4a1440;
  --plum-deep:#3a0f33;
  --plum-mid:#6a1f58;
  --rose:#c45878;
  --rose-soft:#d8839b;
  --blush:#fbe9ee;
  --blush-deep:#f5d3dd;
  --white:#ffffff;
  --photo-a:#2b2a3a;
  --photo-b:#8a6a6a;
}
*{margin:0;padding:0;box-sizing:border-box}
html,body{width:1200px;height:3484px;overflow:hidden}
body{background:var(--sheet);position:relative;font-family:'Montserrat',sans-serif}
.card{position:absolute;width:494px;height:617px;overflow:hidden}
.col-a{left:88px}.col-b{left:630px}
.row-1{top:107px}.row-2{top:766px}.row-3{top:1425px}.row-4{top:2084px}.row-5{top:2742px}
.abs{position:absolute}
.center{text-align:center;left:0;right:0}
.sans{font-family:'Montserrat',sans-serif;font-weight:900;line-height:1}
.serif{font-family:'Playfair Display',serif;font-weight:900;line-height:1}
.slab{font-family:'Playfair Display',serif;font-weight:700;letter-spacing:2px;line-height:1.2}
.pop{font-family:'Poppins',sans-serif;font-weight:700;line-height:1.2}
.it{font-style:italic}
.photo{position:absolute;background:linear-gradient(160deg,var(--photo-b),var(--photo-a));}
.photo.pair{background:linear-gradient(170deg,#d9cfc9 0%,#5a6a8a 45%,#2a3550 100%);border-radius:40px 40px 0 0}
.photo.hug{background:linear-gradient(150deg,#f3d1da,#d64f8f 55%,#7a3a5a)}
.photo.solo{border-radius:120px 120px 0 0}
.over{z-index:2}

/* 1 */
.c1{background:linear-gradient(180deg,var(--plum-mid),var(--plum-deep))}
.c1 .band{right:0;top:0;width:136px;height:100%;background:var(--rose)}
.c1 .frame{left:16px;top:45px;width:440px;height:540px;border:2px solid var(--rose);border-radius:30px}
.c1 .head{left:34px;top:96px;font-size:54px;color:var(--white);line-height:58px}
.c1 .sub{left:28px;top:472px;font-size:32px;color:var(--rose)}
/* 2 */
.c2{background:linear-gradient(180deg,#fff,var(--blush))}
.c2 .top{left:0;top:0;width:100%;height:299px;background:linear-gradient(180deg,var(--plum-deep),var(--plum-mid));border-radius:0 0 70px 0}
.c2 .l1{top:26px;font-size:48px;color:var(--white);font-weight:800}
.c2 .l2{top:84px;font-size:48px;color:var(--white);font-weight:800}
.c2 .l3{top:156px;font-size:52px;color:var(--white)}
.c2 .l4{top:210px;font-size:52px;color:var(--rose)}
.c2 .sub{left:22px;top:342px;font-size:38px;color:var(--plum);line-height:46px}
.c2 .sub .rt{color:var(--rose)}
/* 3 */
.c3{background:linear-gradient(90deg,#efe6e3,#fff 50%,#efe6e3)}
.c3 .box{left:18px;top:16px;width:458px;height:344px;background:linear-gradient(180deg,var(--plum-mid),var(--plum-deep));border-radius:50px}
.c3 .h1{top:52px;font-size:92px;color:var(--white)}
.c3 .h2{top:120px;font-size:90px;color:var(--white)}
.c3 .sub-h{top:214px;font-size:23px;letter-spacing:0;color:var(--rose);font-weight:700}
.c3 .bar{left:0;bottom:0;width:100%;height:59px;background:var(--plum)}
.c3 .bar-t{bottom:14px;font-size:24px;color:var(--white);line-height:1}
/* 4 */
.c4{background:var(--blush)}
.c4 .box{left:181px;top:73px;width:291px;height:521px;background:var(--rose);border-radius:90px 20px 20px 20px}
.c4 .txt{left:181px;width:291px;text-align:center;color:var(--white)}
.c4 .t1{top:136px;font-size:38px;font-weight:800;line-height:46px}
.c4 .t2{top:290px;font-size:124px}
.c4 .t3{top:425px;font-size:54px;font-weight:800;left:170px;width:302px;text-align:center;color:var(--white)}
.c4 .t4{left:120px;width:350px;top:500px;font-size:24px;line-height:30px;letter-spacing:1px;text-align:center;color:var(--white)}
/* 5 */
.c5{background:linear-gradient(180deg,var(--blush) 0 304px,var(--rose) 304px)}
.c5 .box{left:24px;top:27px;width:446px;height:391px;background:linear-gradient(180deg,var(--plum-mid),var(--plum-deep));border-radius:30px}
.c5 .dots{left:34px;top:37px;width:426px;height:371px;border:2px dotted var(--rose-soft);border-radius:24px}
.c5 .h{font-size:56px;color:var(--blush);font-weight:800}
.c5 .h1{top:94px}.c5 .h2{top:167px}
.c5 .s{font-size:54px;color:var(--blush);font-weight:700;line-height:58px;top:240px}
.c5 .sub{top:478px;font-size:40px;color:var(--white);line-height:48px}
/* 6 */
.c6{background:linear-gradient(180deg,var(--rose) 0%,var(--rose-soft) 45%,var(--blush) 80%)}
.c6 .h1{top:22px;font-size:108px;color:var(--white)}
.c6 .h2{top:136px;font-size:52px;color:var(--white);line-height:64px}
.c6 .pill{left:38px;top:496px;width:416px;height:121px;background:var(--plum);border-radius:40px 70px 0 0}
.c6 .pill-t{left:38px;width:416px;top:516px;font-size:33px;color:var(--white);font-weight:600;text-align:center;line-height:40px}
/* 7 */
.c7{background:linear-gradient(180deg,var(--blush),#fff)}
.c7 .box{left:24px;top:31px;width:445px;height:490px;background:var(--rose);border-radius:40px 40px 0 40px}
.c7 .t{left:40px;color:var(--white)}
.c7 .t1{top:90px;font-size:68px}
.c7 .t2{top:160px;font-size:124px}
.c7 .t3{top:290px;font-size:54px;line-height:62px;font-weight:800}
.c7 .sub{top:530px;font-size:31px;color:var(--plum);line-height:36px}
/* 8 */
.c8{background:var(--blush)}
.c8 .box{left:20px;top:20px;width:454px;height:578px;background:linear-gradient(160deg,var(--plum-mid),var(--plum-deep));border-radius:40px 140px 40px 140px}
.c8 .a{font-size:50px;color:var(--blush);top:98px}
.c8 .b{font-size:50px;color:var(--blush);top:180px}
.c8 .c{font-size:64px;color:var(--blush);top:250px}
.c8 .d{font-size:64px;color:var(--blush);top:330px}
.c8 .sub{top:420px;font-size:36px;color:var(--rose);line-height:44px}
/* 9 */
.c9{background:linear-gradient(180deg,#fff,var(--blush))}
.c9 .l{font-size:52px;color:var(--plum);letter-spacing:-1px}
.c9 .l1{top:48px}.c9 .l2{top:122px}.c9 .l3{top:197px;color:var(--rose)}.c9 .l4{top:265px;color:var(--rose)}.c9 .l5{top:328px;font-size:48px}
.c9 svg{position:absolute;left:0;top:360px}
.c9 .sub{top:475px;font-size:43px;color:var(--white);line-height:50px}
/* 10 */
.c10{background:var(--blush)}
.c10 .top{left:0;top:0;width:100%;height:376px;background:linear-gradient(180deg,var(--plum-deep),var(--plum-mid))}
.c10 .a{top:55px;font-size:52px;color:var(--white)}
.c10 .b{top:128px;font-size:52px;color:var(--white)}
.c10 .c{top:194px;font-size:62px;color:var(--white)}
.c10 .pill{left:20px;top:559px;width:456px;height:38px;background:var(--rose);border-radius:19px;border:2px solid var(--white)}
.c10 .pill-t{left:20px;width:456px;top:566px;text-align:center;font-size:23px;color:var(--white);line-height:24px;font-weight:700}
</style>
</head>
<body>

<section class="card col-a row-1 c1">
  <div class="abs band"></div>
  <div class="abs frame"></div>
  <div class="photo solo" style="left:300px;top:28px;width:194px;height:589px" role="img" aria-label="Photo of RT, smiling woman in a black top and jeans, hand on hip"></div>
  <h2 class="abs sans head over">STOP<br>STARTING<br>OVER<br>EVERY<br>MONDAY</h2>
  <p class="abs slab sub over">Stay Consistent with<br>RT in Your Pocket!</p>
</section>

<section class="card col-b row-1 c2">
  <div class="abs top"></div>
  <p class="abs center sans l1">You don't need</p>
  <p class="abs center sans l2">more will power.</p>
  <p class="abs center sans l3">YOU NEED</p>
  <p class="abs center sans it l4">MORE SUPPORT</p>
  <div class="photo hug" style="left:208px;top:278px;width:286px;height:339px;border-radius:60px 0 0 0" role="img" aria-label="Photo of two women hugging and laughing"></div>
  <p class="abs slab sub over">Stay<br>Consistent<br>with <span class="rt">RT</span><br><span class="rt">in Your<br>Pocket!</span></p>
</section>

<section class="card col-a row-2 c3">
  <div class="abs box"></div>
  <p class="abs center serif h1">Built for</p>
  <p class="abs center serif it h2">women</p>
  <p class="abs center slab it sub-h">who are tired of doing this alone</p>
  <div class="photo pair" style="left:115px;top:250px;width:310px;height:310px" role="img" aria-label="Photo of two women in denim laughing together"></div>
  <div class="abs bar"></div>
  <p class="abs center pop it bar-t">Stay Consistent with RT in Your Pocket!</p>
</section>

<section class="card col-b row-2 c4">
  <div class="abs box"></div>
  <div class="photo solo" style="left:0;top:32px;width:235px;height:585px" role="img" aria-label="Photo of RT, smiling woman in a black top, hand on hip"></div>
  <p class="abs txt sans t1 over">When<br>Motivation<br>Fades,</p>
  <p class="abs txt serif t2 over">RT</p>
  <p class="abs sans t3 over">Checks In</p>
  <p class="abs slab it t4 over">Stay Consistent<br>with RT in Your Pocket!</p>
</section>

<section class="card col-a row-3 c5">
  <div class="abs box"></div>
  <div class="abs dots"></div>
  <p class="abs center sans h h1">THE SUPPORT</p>
  <p class="abs center sans h h2">SYSTEM</p>
  <p class="abs center serif it s">You've Been<br>Missing</p>
  <p class="abs center pop sub">Stay Consistent with<br>RT in Your Pocket!</p>
</section>

<section class="card col-b row-3 c6">
  <p class="abs center serif h1">Support</p>
  <p class="abs center serif it h2">When Motivation<br>Disappears</p>
  <div class="photo pair" style="left:73px;top:272px;width:338px;height:234px" role="img" aria-label="Photo of two women in denim laughing together"></div>
  <div class="abs pill"></div>
  <p class="abs pop pill-t">Stay Consistent with<br>RT in Your Pocket!</p>
</section>

<section class="card col-a row-4 c7">
  <div class="abs box"></div>
  <div class="photo solo" style="left:300px;top:54px;width:194px;height:467px" role="img" aria-label="Photo of RT, smiling woman in a black top pointing"></div>
  <p class="abs sans t t1 over">What if</p>
  <p class="abs serif t t2 over">RT</p>
  <p class="abs sans t t3 over">Checked<br>in Every<br>Day?</p>
  <p class="abs center slab it sub">Stay Consistent with<br>RT in Your Pocket!</p>
</section>

<section class="card col-b row-4 c8">
  <div class="abs box"></div>
  <p class="abs center sans a">THE MISSING</p>
  <p class="abs center sans b">PIECE ISN'T</p>
  <p class="abs center sans c">ANOTHER</p>
  <p class="abs center sans d">DIET</p>
  <p class="abs center slab sub">Stay Consistent with<br>RT in Your Pocket!</p>
</section>

<section class="card col-a row-5 c9">
  <p class="abs center sans l l1">EAT THE FOOD</p>
  <p class="abs center sans l l2">YOU LOVE.</p>
  <p class="abs center sans l l3">STAY</p>
  <p class="abs center sans l l4">ACCOUNTABLE</p>
  <p class="abs center sans l l5">EVERY DAY</p>
  <svg width="494" height="257" viewBox="0 0 494 257">
    <path d="M0 30 C120 55 150 110 494 70 L494 257 L0 257 Z" fill="var(--plum)"/>
    <path d="M0 95 C140 115 300 45 494 80 L494 257 L0 257 Z" fill="var(--rose)"/>
  </svg>
  <p class="abs center slab it sub">Stay Consistent with<br>RT in Your Pocket!</p>
</section>

<section class="card col-b row-5 c10">
  <div class="abs top"></div>
  <p class="abs center sans a">ONE BAD MEAL</p>
  <p class="abs center sans b">DOESN'T MEAN</p>
  <p class="abs center sans c">YOU FAILED</p>
  <div class="photo pair" style="left:46px;top:266px;width:393px;height:351px" role="img" aria-label="Photo of two women in denim laughing together"></div>
  <div class="abs pill"></div>
  <p class="abs serif it pill-t">Stay Consistent with RT in Your Pocket!</p>
</section>

</body>
</html>
```